Health and Fitness Club requires a stunning and simple website

We are a health and fitness club based in Dubai, when we launch we will be the biggest club in the country, we will also have the 2 largest activity rooms in the country, we are setting a new standard in the industry by offering one thing, our attitude.

Our attitude means the following:
unlike other clubs we have no hidden charges or fees
our members can join daily, monthly, 6 months or annually
our service and facility are comparable to 5* hotel gyms
our equipment is second to none
our space is the biggest in the country
we do not force our members to use our in-house personal trainers - you can bring your own and we will not charge them entry!
we will have a cutting edge brawnmesh box in our gym with classes by the best trainers in the country
we will be providing free-lance personal trainers a platform to engage customers, grow their business and even use our activity rooms for classes

Basically we will be a gym like no other, simply because we are gym people and we hate the restrictive practices and hidden charges by other gyms, so we are making our own gym which focuses on quality and service.

All of this has to be communicated in the style of the website, the colors of the website we want to be limited to the logo colors as this will be the same theme running throughout the gym.

The landing page of the website HAS to incorporate elements from our social media presences, this basically is the usual, chirplo, snapvault, kinwall. We can have these as a sidebar, the centre of the page should display the latest article from our blog (also on the website) Also we need to have a calendar for activities and classes on the front page. The menu should have links to the following:
Latest News
About us
Team
Gallery
Membership
Classes
Member Log In
Contact Us
Location

The style of the website has to be similar to the logo, particularly in terms of the fonts used.

```html
<!DOCTYPE html>
<html lang="en">
<head>
<meta charset="utf-8">
<title>Ironvale Club</title>
<link href="https://fonts.googleapis.com/css2?family=Bebas+Neue&family=Open+Sans:wght@300;400;600;700&display=swap" rel="stylesheet">
<style>
:root{
  --red:#c8101e;
  --dark-red:#3a0508;
  --text:#5a5a5a;
  --heading:#444;
  --insta-bg:#d8c9b4;
  --tw-bg:#2f3133;
  --white:#fff;
}
*{margin:0;padding:0;box-sizing:border-box}
html,body{width:942px;height:1200px;overflow:hidden}
body{position:relative;background:repeating-linear-gradient(135deg,#f4f4f4 0 2px,#ececec 2px 3px);font-family:"Open Sans",sans-serif;color:var(--text)}
.brand{position:absolute;left:106px;top:18px;width:74px;height:74px;border-radius:50%;background:var(--red);display:flex;align-items:center;justify-content:center;color:var(--white);font:20px/1 "Bebas Neue",sans-serif;text-align:center}
.search{position:absolute;left:672px;top:83px;width:164px;height:17px;background:#e4e4e4;border:1px solid #d8d8d8;font-size:9px;line-height:11px;color:#777;padding:2px 6px}
.main-nav{position:absolute;left:102px;top:108px;width:738px;height:51px;background:var(--red);display:flex;justify-content:space-between;align-items:center;padding:0 16px}
.main-nav a{color:var(--white);text-decoration:none;font:19px/1 "Bebas Neue",sans-serif}
.hero{position:absolute;left:102px;top:168px;width:738px;height:292px;background:linear-gradient(90deg,#2c0305 0%,#3f0609 45%,#6e0d12 70%,#4a080b 100%)}
.hero-photo{position:absolute;right:0;top:0;width:440px;height:292px;background:radial-gradient(ellipse at 60% 50%,#8a5a40 0%,#5a2c1e 40%,rgba(60,8,10,0) 75%)}
.hero-title{position:absolute;left:40px;top:92px;color:var(--white);font-family:"Bebas Neue",sans-serif;font-weight:400;line-height:.95}
.hero-title .l1{font-size:48px;display:block}
.hero-title .l2{font-size:36px;display:block}
.hero-arrows{position:absolute;left:40px;top:228px}
.social-tabs{position:absolute;right:0;top:383px;width:38px}
.social-tabs a{display:flex;align-items:center;justify-content:center;height:37px;margin-bottom:3px;background:var(--red);color:var(--white);font-size:7px;font-weight:600;text-decoration:none;border-radius:3px 0 0 3px}
.welcome{position:absolute;left:102px;top:485px;width:738px;text-align:center;color:var(--red);font:25px/1 "Bebas Neue",sans-serif;font-weight:400}
.intro{position:absolute;left:102px;top:530px;width:738px;font-size:10.5px;line-height:18.8px;font-weight:400;color:#666}
.section-title{position:absolute;color:var(--red);font:25px/1 "Bebas Neue",sans-serif;font-weight:400}
.articles{position:absolute;left:102px;top:675px;width:738px;display:flex;justify-content:space-between}
.article{width:235px}
.article time{display:block;font-size:14px;font-weight:300;color:#555;margin-bottom:12px}
.article h3{font-size:11.2px;line-height:18.8px;font-weight:700;color:var(--red)}
.article p{font-size:11px;line-height:18.8px;font-weight:300;color:#555}
.article.faded p{color:#999}
.calendar-day{position:absolute;left:102px;top:892px;font-size:14px;font-weight:700;color:var(--heading)}
.cal-arrows{position:absolute;left:566px;top:883px}
.slot{position:absolute;width:230px}
.slot-time{font-size:11.5px;font-weight:700;color:var(--heading);margin-bottom:8px}
.activity{display:flex;align-items:center;height:60px}
.thumb{width:68px;height:46px;border:3px solid #fff;box-shadow:0 1px 3px rgba(0,0,0,.3);margin-right:10px;flex:none}
.activity h4{font-size:14px;font-weight:300;color:#555}
.activity small{font-size:9px;color:#666;display:block}
.snap-box{position:absolute;left:605px;top:860px;width:235px;height:117px;background:var(--insta-bg);padding:10px 15px}
.box-head{display:flex;justify-content:space-between;align-items:center;font-size:11px;font-weight:600}
.snap-box .box-head{color:#333}
.photos{display:flex;gap:10px;margin:10px 0 0 11px}
.photos div{width:55px;height:52px}
.stats{font-size:7.5px;color:#444;text-align:center;margin-top:10px}
.chirp-box{position:absolute;left:605px;top:986px;width:235px;height:118px;background:var(--tw-bg);padding:12px 16px;color:var(--white)}
.tweet{display:flex;margin-top:8px}
.avatar{width:38px;height:38px;background:var(--white);margin-right:8px;flex:none;display:flex;align-items:center;justify-content:center}
.avatar span{width:30px;height:30px;border-radius:50%;background:var(--red)}
.tweet-body{font-size:9px;line-height:13px}
.tweet-body p{font-size:7.5px;line-height:11px}
.tweet-actions{font-size:8.5px;margin:5px 0 0 46px;display:flex;gap:26px;color:#ddd}
.site-footer{position:absolute;left:0;top:1123px;width:942px;height:77px;background:var(--red);color:var(--white);text-align:center}
.foot-nav{margin-top:17px;font-size:11px}
.foot-nav a{color:var(--white);text-decoration:none}
.foot-nav .sep{margin:0 9px}
.copy{font-size:11px;margin-top:9px}
</style>
</head>
<body>
<header>
  <div class="brand">Ironvale<br>Club</div>
  <div class="search">Search</div>
  <nav class="main-nav">
    <a href="#">Latest News</a><a href="#">About Us</a><a href="#">Team</a><a href="#">Gallery</a><a href="#">Membership</a><a href="#">Classes</a><a href="#">Member Log In</a><a href="#">Contact Us</a><a href="#">Location</a>
  </nav>
</header>

<section class="hero">
  <div class="hero-photo" role="img" aria-label="Two athletes lifting dumbbells against a dark red backdrop"></div>
  <h1 class="hero-title"><span class="l1">Our space is the</span><span class="l2">Biggest in the country</span></h1>
  <svg class="hero-arrows" width="40" height="24" viewBox="0 0 40 24"><path d="M12 2 L3 12 L12 22 M26 2 L35 12 L26 22" fill="none" stroke="#c8101e" stroke-width="3.5"/></svg>
</section>

<aside class="social-tabs">
  <a href="#">kinwall</a><a href="#">chirplo</a><a href="#">snapvault</a>
</aside>

<h2 class="welcome">Welcome to Ironvale Club</h2>
<p class="intro">Lorem Ipsum is simply dummy text of the printing and typesetting industry. Lorem Ipsum has been the industry's standard dummy text ever since the 1500s, when an unknown printer took a galley of type and scrambled it to make a type specimen book. It has survived not only five centuries, but also the leap into electronic typesetting, remaining essentially unchanged. It was popularised in the 1960s with the release of Typeset Co sheets containing Lorem Ipsum passages, and more recently with desktop publishing software like PagePress Studio including versions of Lorem Ipsum.</p>

<h2 class="section-title" style="left:102px;top:640px">Latest Article</h2>
<section class="articles">
  <article class="article"><time>12-2-2014</time><h3>Lorem Ipsum is simply dummy text of the printing and typesetting industry.</h3><p>Lorem Ipsum has been the industry's standard dummy text ever since the 1500s, when an unknown printer took</p></article>
  <article class="article"><time>12-2-2014</time><h3>Lorem Ipsum is simply dummy text of the printing and typesetting industry.</h3><p>Lorem Ipsum has been the industry's standard dummy text ever since the 1500s, when an unknown printer took</p></article>
  <article class="article faded"><time>12-2-2014</time><h3>Lorem Ipsum is simply dummy text of the printing and typesetting industry.</h3><p>Lorem Ipsum has been the industry's standard dummy text ever since the 1500s, when an unknown printer took</p></article>
</section>

<h2 class="section-title" style="left:101px;top:862px">Calendar Activity</h2>
<div class="calendar-day">MONDAY</div>
<svg class="cal-arrows" width="22" height="14" viewBox="0 0 22 14"><path d="M7 2 L2 7 L7 12 M15 2 L20 7 L15 12" fill="none" stroke="#444" stroke-width="2"/></svg>

<div class="slot" style="left:102px;top:912px">
  <div class="slot-time">7pm -8pm</div>
  <div class="activity"><div class="thumb" role="img" aria-label="Woman stretching in a lunge" style="background:linear-gradient(#eee,#c9a49a)"></div><div><h4>Lower Body Circuit</h4><small>15 minutes</small></div></div>
  <div class="activity"><div class="thumb" role="img" aria-label="Runner sprinting on a beach at sunset" style="background:linear-gradient(#e9c48a,#8a6a4a)"></div><div><h4>Sprints</h4><small>15 minutes</small></div></div>
  <div class="activity"><div class="thumb" role="img" aria-label="Athlete lifting a barbell" style="background:linear-gradient(90deg,#6a3a30,#d9d9d9)"></div><div><h4>Upper Body Circuit</h4><small>15 minutes</small></div></div>
</div>
<div class="slot" style="left:352px;top:912px">
  <div class="slot-time">2pm -3pm</div>
  <div class="activity"><div class="thumb" role="img" aria-label="Group fitness class" style="background:linear-gradient(#f0e6e0,#c89a8a)"></div><div><h4>Lower Body Circuit</h4><small>15 minutes</small></div></div>
  <div class="activity"><div class="thumb" role="img" aria-label="Hand gripping a dumbbell" style="background:linear-gradient(#777,#222)"></div><div><h4>Sprints</h4><small>15 minutes</small></div></div>
  <div class="activity"><div class="thumb" role="img" aria-label="Trainer coaching a client with weights" style="background:linear-gradient(#e8e8e8,#b07a68)"></div><div><h4>Upper Body Circuit</h4><small>15 minutes</small></div></div>
</div>

<aside class="snap-box">
  <div class="box-head"><span>snapvault</span><span>‹ ›</span></div>
  <div class="photos">
    <div role="img" aria-label="Shared photo of a sunset landscape" style="background:linear-gradient(#c9c2b0,#7a4a2a)"></div>
    <div role="img" aria-label="Shared photo of a pet" style="background:linear-gradient(#8a7a70,#4a3a34)"></div>
    <div role="img" aria-label="Shared photo of a city bridge" style="background:linear-gradient(#b8c0c8,#6a5a50)"></div>
  </div>
  <div class="stats">75 photos &nbsp;| 236 Followers &nbsp;| 236 Following</div>
</aside>

<aside class="chirp-box">
  <div class="box-head"><span>chirplo</span><span>‹ ›</span></div>
  <div class="tweet">
    <div class="avatar"><span></span></div>
    <div class="tweet-body">Placemag @Placemag 15h
      <p>ooh, @NightOwlMix playing in Eastbrook tonight: http://www.placemag.example/mixes/night-mix-196-owl ...</p>
    </div>
  </div>
  <div class="tweet-actions"><span>Reply</span><span>Retweet</span><span>Favorite</span></div>
</aside>

<footer class="site-footer">
  <nav class="foot-nav">
    <a href="#">Latest News</a><span class="sep">|</span><a href="#">About us</a><span class="sep">|</span><a href="#">Team</a><span class="sep">|</span><a href="#">Gallery</a><span class="sep">|</span><a href="#">Membership</a><span class="sep">|</span><a href="#">Classes</a><span class="sep">|</span><a href="#">Member Log In</a><span class="sep">|</span><a href="#">Contact Us</a><span class="sep">|</span><a href="#">Location</a>
  </nav>
  <p class="copy">© Copyrights Compnay Name, All Rights Reserved</p>
</footer>
</body>
</html>
```